Berufora Banner Design (Profilbanner und Unternehmensbanner) (1584 x 396) (1128 x 191)
Zielgruppe
Ich bin Dienstleister und Unternehmensberater für technischen B2B Vertrieb.
Für meinen BeruFora Account suche ich einen Banner für meine Profilseite und einen Banner für die Unternehmensseite). Meine Zielgruppe sind leitende Angestellte in Unternehmen. Das Design sollte entsprechend grafisch hochwertig, seriös gestaltet sein.
I am a service provider and management consultant for technical B2B sales.
For my BeruFora account, I'm looking for a banner for my profile page and a banner for the company page). My target group are executives in companies. The design should have a correspondingly high-quality graphic design and be serious.
Aufgabenstellung
Wichtig ist die Berücksichtigung meines Logos (PNG im Anhang) und des Corporate Identity Farben (PDF Anhang und unten stehend). Stock Bilder oder Grafiken können/sollen gerne mit eingebunden werden. Wichtig ist hier der passende Gesamteindruck.
It is important to consider my logo (PNG in the attachment) and the corporate identity colors (PDF attachment and below). Stock images or graphics can/should be included. The right overall impression is important here.
HEX / HTML 002854
HEX / HTML 00b6e3
Bannergrößen / Banner sizes
Profilbanner (1584 x 396)
Unternehmensseitenbanner (1128 x 191)

```html
<!DOCTYPE html>
<html lang="de">
<head>
<meta charset="UTF-8">
<title>Matthias Brandt – Profilbanner</title>
<link rel="stylesheet" href="https://fonts.googleapis.com/css2?family=Titillium+Web:wght@400;600;700&display=swap">
<style>
  :root {
    --stage: #cfcfcf;
    --banner-dark: #1b1c26;
    --banner-mid: #2a2b37;
    --text-light: #ffffff;
    --engine-light: #9a9ca6;
    --engine-dark: #15161d;
  }
  * { margin: 0; padding: 0; box-sizing: border-box; }
  html, body { width: 1200px; height: 675px; overflow: hidden; }
  body {
    background: var(--stage);
    font-family: "Titillium Web", sans-serif;
    position: relative;
  }
  .banner {
    position: absolute;
    left: 0; top: 187px;
    width: 1200px; height: 300px;
    background: linear-gradient(100deg, var(--banner-mid) 0%, var(--banner-dark) 60%, var(--banner-dark) 100%);
    overflow: hidden;
    color: var(--text-light);
  }
  .engine-visual {
    position: absolute;
    left: 700px; top: 0;
    width: 500px; height: 300px;
    background:
      radial-gradient(ellipse at 45% 60%, var(--engine-light) 0%, #5c5e68 30%, #2b2c35 60%, transparent 80%),
      linear-gradient(90deg, transparent 0%, var(--engine-dark) 30%);
    -webkit-mask-image: linear-gradient(90deg, transparent 0%, #000 22%);
    mask-image: linear-gradient(90deg, transparent 0%, #000 22%);
  }
  .headline {
    position: absolute;
    left: 201px; top: 66px;
    text-transform: uppercase;
    line-height: 1;
  }
  .headline-line { display: block; white-space: nowrap; }
  .headline-line--second { margin-left: 37px; margin-top: 12px; }
  .headline .light { font-weight: 400; font-size: 34px; letter-spacing: -0.5px; }
  .headline .strong { font-weight: 700; font-size: 46px; letter-spacing: -0.5px; }
  .contact-row {
    position: absolute;
    left: 238px; top: 249px;
    display: flex; align-items: center; gap: 22px;
    font-size: 15px; font-weight: 600;
  }
  .contact-item { display: flex; align-items: center; gap: 8px; white-space: nowrap; }
  .contact-item svg { width: 24px; height: 24px; }
</style>
</head>
<body>
  <section class="banner" aria-label="Profilbanner">
    <div class="engine-visual" role="img" aria-label="Foto eines Automotors mit Riemenscheiben in Schwarz-Weiß"></div>

    <h1 class="headline">
      <span class="headline-line"><span class="light">Volle </span><span class="strong">Power</span></span>
      <span class="headline-line headline-line--second"><span class="light">Für ihr </span><span class="strong">Business</span><span class="light">.</span></span>
    </h1>

    <div class="contact-row">
      <span class="contact-item">
        <svg viewBox="0 0 24 24" fill="none" stroke="currentColor" stroke-width="1.4" stroke-linejoin="round" aria-hidden="true">
          <path d="M5 3l4 1 1.5 4.5-2.3 1.6a11 11 0 0 0 5.7 5.7l1.6-2.3L20 15l1 4-2 2C10 21 3 14 3 5z"/>
        </svg>
        0987 | 654 321 0
      </span>
      <span class="contact-item">
        <svg viewBox="0 0 24 24" fill="none" stroke="currentColor" stroke-width="1.4" aria-hidden="true">
          <circle cx="12" cy="12" r="10"/>
          <ellipse cx="12" cy="12" rx="4.5" ry="10"/>
          <path d="M2 12h20M4 6.5h16M4 17.5h16M12 2v20"/>
        </svg>
        MATTHIASBRANDT.DE
      </span>
    </div>
  </section>
</body>
</html>
```